Clean business card with logo provided

I want a card that will stand out among the masses. I need the color and image to show professionalism and yet have a family appeal showing that I only deal with win/win scenarios. The back of the card will be used to take notes about the individual so I can use that in my database entry. I like modern design but need professionalism in it also. It needs to fit my "clean, safe, and affordable housing" motto. I need to be able to write on the file and update the card details for my employees.

Target Market(s)

Investors looking to make investment income through real estate

Industry/Entity Type

Real Estate

Contact Information for Business Card

Brent Kovalich
blank address, city, st, zip code
480-555-3174
brentkovalich@ridgeworthrentals.example
www.ridgeworthrentals.example

Font styles to use
Sans Serif

Requirements
Must have
• I would like the back of the card to have lines for info. example
• Met/Visited: Date:
• Interets:
Nice to have
• I want the cards color to match the logo background color. Font with details to be san serif and black. I want the card rectangular with square corners. Standard business card size. I would like to see cards designed with both images to see which i prefer more.

```html
<!DOCTYPE html>
<html lang="en">
<head>
<meta charset="utf-8">
<title>Ridgeworth Rentals – Business Card</title>
<link href="https://fonts.googleapis.com/css2?family=Open+Sans:wght@400;600;700&display=swap" rel="stylesheet">
<style>
  :root {
    --teal: #00b3cb;
    --teal-dark: #0aa7bd;
    --ink: #111111;
    --paper: #ffffff;
    --backdrop: #e9e6e3;
  }
  * { margin: 0; padding: 0; box-sizing: border-box; }
  html, body { width: 1200px; height: 900px; overflow: hidden; }
  body {
    background: var(--backdrop);
    font-family: "Open Sans", Arial, sans-serif;
    position: relative;
  }
  .card {
    position: absolute;
    width: 593px;
    height: 364px;
    background: var(--paper);
    border-radius: 16px;
    overflow: hidden;
    box-shadow: 0 6px 22px rgba(0,0,0,0.18);
  }
  /* Front */
  .card-front { left: 192px; top: 78px; }
  .holder-name {
    position: absolute; top: 28px; width: 100%;
    text-align: center; color: var(--teal);
    font-weight: 700; font-size: 21px; letter-spacing: 0.5px;
  }
  .brand {
    position: absolute; top: 96px; left: 0; width: 100%;
    text-align: center;
  }
  .brand-name {
    display: inline-flex; align-items: center; gap: 12px;
    color: var(--teal); font-weight: 700; font-size: 34px; letter-spacing: 2px;
  }
  .brand-mark {
    width: 26px; height: 26px; border-radius: 50%; background: var(--teal);
  }
  .motto {
    position: absolute; top: 172px; left: 153px;
    color: var(--teal); font-size: 10.5px; font-weight: 600;
  }
  .contact-list {
    position: absolute; top: 214px; width: 100%;
    list-style: none; text-align: center;
    color: var(--ink); font-size: 16px; line-height: 25px;
  }
  .contact-list li { display: flex; justify-content: center; align-items: center; gap: 4px; }
  .contact-list svg { width: 13px; height: 13px; fill: var(--teal); }
  .address-band {
    position: absolute; left: 0; bottom: 0; width: 100%; height: 69px;
    background: var(--teal); color: var(--paper);
    display: flex; align-items: center; justify-content: center;
    font-weight: 600; font-size: 16px;
  }
  /* Back */
  .card-back { left: 509px; top: 486px; }
  .back-band {
    position: absolute; top: 0; left: 0; width: 100%; height: 66px; background: var(--teal);
  }
  .back-rule {
    position: absolute; top: 70px; left: 0; width: 100%; height: 2px; background: var(--teal);
  }
  .note-field { position: absolute; left: 168px; width: 300px; }
  .note-label {
    text-align: center; color: var(--teal-dark);
    font-weight: 700; font-size: 18px; width: 300px; margin-left: -150px; position: relative; left: 150px;
  }
  .note-line {
    margin-top: 32px; width: 288px; height: 1.5px; background: var(--ink);
  }
  .field-date { top: 90px; }
  .field-interests { top: 171px; }
  .field-problems { top: 251px; }
  .field-problems .note-line { margin-top: 40px; }
</style>
</head>
<body>

<section class="card card-front" aria-label="Business card front">
  <h1 class="holder-name">BRENT KOVALICH</h1>
  <div class="brand">
    <span class="brand-name">RIDGEWORTH RENTALS LLC <span class="brand-mark"></span></span>
  </div>
  <p class="motto">Providing clean, safe, and affordable housing</p>
  <ul class="contact-list">
    <li>
      <svg viewBox="0 0 24 24" aria-hidden="true"><path d="M6.6 10.8a15.1 15.1 0 0 0 6.6 6.6l2.2-2.2c.3-.3.7-.4 1-.2 1.1.4 2.3.6 3.6.6.6 0 1 .4 1 1V20c0 .6-.4 1-1 1A17 17 0 0 1 3 4c0-.6.4-1 1-1h3.5c.6 0 1 .4 1 1 0 1.3.2 2.5.6 3.6.1.3 0 .7-.2 1z"/></svg>
      480-555-3174
    </li>
    <li>
      <svg viewBox="0 0 24 24" aria-hidden="true"><path d="M2 5h20v14H2z" /><path d="M2 5l10 7 10-7" fill="none" stroke="#fff" stroke-width="2"/></svg>
      brentkovalich@ridgeworthrentals.example
    </li>
    <li>
      <svg viewBox="0 0 24 24" aria-hidden="true"><circle cx="12" cy="12" r="10"/><path d="M2 12h20M12 2c3 3 3 17 0 20M12 2c-3 3-3 17 0 20" fill="none" stroke="#fff" stroke-width="1.5"/></svg>
      www.ridgeworthrentals.example
    </li>
  </ul>
  <div class="address-band">12345, Address Goes Here Country Name, 123456</div>
</section>

<section class="card card-back" aria-label="Business card back">
  <div class="back-band"></div>
  <div class="back-rule"></div>
  <div class="note-field field-date">
    <p class="note-label">VISITED DATE</p>
    <div class="note-line"></div>
  </div>
  <div class="note-field field-interests">
    <p class="note-label">INTERETS</p>
    <div class="note-line"></div>
  </div>
  <div class="note-field field-problems">
    <p class="note-label">PROBLEMS</p>
    <div class="note-line"></div>
  </div>
</section>

</body>
</html>
```